Clean business card with logo provided

I want a card that will stand out among the masses. I need the color and image to show professionalism and yet have a family appeal showing that I only deal with win/win scenarios. The back of the card will be used to take notes about the individual so I can use that in my database entry. I like modern design but need professionalism in it also. It needs to fit my "clean, safe, and affordable housing" motto. I need to be able to write on the file and update the card details for my employees.

Target Market(s)

Investors looking to make investment income through real estate

Industry/Entity Type

Real Estate

Contact Information for Business Card

Brent Kovalich
blank address, city, st, zip code
480-555-3174
brentkovalich@ridgeworthrentals.example
www.ridgeworthrentals.example

Font styles to use
Sans Serif

Requirements
Must have
• I would like the back of the card to have lines for info. example
• Met/Visited: Date:
• Interets:
Nice to have
• I want the cards color to match the logo background color. Font with details to be san serif and black. I want the card rectangular with square corners. Standard business card size. I would like to see cards designed with both images to see which i prefer more.

```html
<!DOCTYPE html>
<html lang="en">
<head>
<meta charset="UTF-8">
<title>Ridgeworth Rentals LLC – Business Card</title>
<link rel="stylesheet" href="https://fonts.googleapis.com/css2?family=Open+Sans:wght@400;600&display=swap">
<style>
  :root {
    --teal: #00b5cc;
    --white: #ffffff;
    --ink: #1a1a1a;
    --backdrop: #ecebe9;
  }
  * { margin: 0; padding: 0; box-sizing: border-box; }
  html, body {
    width: 1200px;
    height: 900px;
    overflow: hidden;
    background: var(--backdrop);
    font-family: "Open Sans", sans-serif;
  }
  .canvas { position: relative; width: 1200px; height: 900px; }

  .card {
    position: absolute;
    border-radius: 14px;
    overflow: hidden;
    box-shadow: 0 6px 18px rgba(0,0,0,0.12);
  }
  .card--front { left: 78px; top: 35px; width: 588px; height: 363px; background: var(--white); }
  .card--back  { left: 389px; top: 506px; width: 565px; height: 350px; background: var(--teal); }

  .band { position: absolute; left: 0; right: 0; }
  .card--front .band { top: 28px; height: 99px; background: var(--teal); }
  .card--back .band  { top: 80px; height: 98px; background: var(--white); }

  .logo-pill {
    position: absolute;
    border-radius: 60px;
    display: flex;
    flex-direction: column;
    align-items: center;
    justify-content: center;
    gap: 7px;
  }
  .card--front .logo-pill { left: 135px; top: 0; width: 319px; height: 99px; background: var(--white); color: var(--teal); }
  .card--back .logo-pill  { left: 89px;  top: 0; width: 370px; height: 98px; background: var(--teal); color: var(--white); }

  .brand-row { display: flex; align-items: center; gap: 8px; }
  .brand-name {
    font-weight: 600;
    font-size: 15px;
    letter-spacing: 1px;
    white-space: nowrap;
  }
  .card--back .brand-name { font-size: 17px; letter-spacing: 1.5px; }
  .brand-dot { width: 11px; height: 11px; border-radius: 50%; background: currentColor; }
  .card--back .brand-dot { width: 12px; height: 12px; }
  .tagline { font-weight: 600; font-size: 10.5px; white-space: nowrap; }
  .card--back .tagline { font-size: 11.5px; }

  .details {
    position: absolute;
    left: 0; right: 0; top: 176px;
    text-align: center;
    color: var(--ink);
  }
  .person-name {
    color: var(--teal);
    font-weight: 600;
    font-size: 20px;
    letter-spacing: 0.5px;
    margin-bottom: 18px;
  }
  .contact-list { list-style: none; font-size: 15.5px; line-height: 25px; }
  .contact-list li { display: flex; align-items: center; justify-content: center; gap: 5px; }
  .contact-icon { width: 12px; height: 12px; fill: var(--teal); }
  .address { margin-top: 16px; font-size: 15.5px; }

  .notes {
    position: absolute;
    left: 40px; right: 40px; top: 204px;
    color: var(--white);
    font-size: 13px;
    font-weight: 600;
  }
  .note-row { display: flex; gap: 24px; margin-bottom: 16px; }
  .note-field {
    flex: 1;
    display: flex;
    align-items: flex-end;
    gap: 8px;
    height: 22px;
  }
  .note-field--short { flex: 0 0 170px; }
  .note-line { flex: 1; border-bottom: 1.5px solid var(--white); height: 100%; }
</style>
</head>
<body>
<div class="canvas">

  <section class="card card--front" aria-label="Business card front">
    <div class="band">
      <div class="logo-pill">
        <div class="brand-row">
          <span class="brand-name">RIDGEWORTH RENTALS LLC</span>
          <span class="brand-dot"></span>
        </div>
        <span class="tagline">Providing clean, safe, and affordable housing</span>
      </div>
    </div>
    <div class="details">
      <h1 class="person-name">BRENT KOVALICH</h1>
      <ul class="contact-list">
        <li>
          <svg class="contact-icon" viewBox="0 0 24 24" aria-hidden="true"><path d="M6.6 10.8a15 15 0 0 0 6.6 6.6l2.2-2.2a1 1 0 0 1 1-.25 11.4 11.4 0 0 0 3.6.57 1 1 0 0 1 1 1V20a1 1 0 0 1-1 1A17 17 0 0 1 3 4a1 1 0 0 1 1-1h3.5a1 1 0 0 1 1 1c0 1.25.2 2.45.57 3.57a1 1 0 0 1-.25 1z"/></svg>
          480-555-3174
        </li>
        <li>
          <svg class="contact-icon" viewBox="0 0 24 24" aria-hidden="true"><path d="M2 5h20v14H2z M3 6l9 7 9-7" stroke="#fff" stroke-width="1.5"/></svg>
          brentkovalich@ridgeworthrentals.example
        </li>
        <li>
          <svg class="contact-icon" viewBox="0 0 24 24" aria-hidden="true"><circle cx="12" cy="12" r="10"/><path d="M2 12h20M12 2c3 3 3 17 0 20M12 2c-3 3-3 17 0 20" stroke="#fff" stroke-width="1.3" fill="none"/></svg>
          www.ridgeworthrentals.example
        </li>
      </ul>
      <p class="address">12345, Address Goes Here Country Name, 123456</p>
    </div>
  </section>

  <section class="card card--back" aria-label="Business card back">
    <div class="band">
      <div class="logo-pill">
        <div class="brand-row">
          <span class="brand-name">RIDGEWORTH RENTALS LLC</span>
          <span class="brand-dot"></span>
        </div>
        <span class="tagline">Providing clean, safe, and affordable housing</span>
      </div>
    </div>
    <div class="notes">
      <div class="note-row">
        <div class="note-field"><span>Met/Visited:</span><span class="note-line"></span></div>
        <div class="note-field note-field--short"><span>Date:</span><span class="note-line"></span></div>
      </div>
      <div class="note-row">
        <div class="note-field"><span>Interests:</span><span class="note-line"></span></div>
      </div>
      <div class="note-row">
        <div class="note-field"><span class="note-line"></span></div>
      </div>
    </div>
  </section>

</div>
</body>
</html>
```